Upmarket Dessert Lounge needs a Business Card Design

We are an upmarket dessert lounge needing a business card to match our image.

We want something that is simple yet beautiful, feminine, classy, sophisticated and elegant. We want it to stand out and don't mind if it is bold.

The design should include our logo and colours of red or maroon with gold highlights. We don't mind if black is used.

Marlow & Quince

Target Market(s)

For those who like to indulge or treat themselves and give in to their temptations on good quality desserts.

Industry/Entity Type

Business

Requirements
Must have
• Must include our logo and our name

Marlow & Quince

M & Q

```html
<!DOCTYPE html>
<html lang="en">
<head>
<meta charset="utf-8">
<title>Marlow &amp; Quince — Business Card</title>
<link rel="stylesheet" href="https://fonts.googleapis.com/css2?family=Tinos:wght@400;700&display=swap">
<style>
  :root {
    --backdrop: #ece6df;
    --navy: #040c22;
    --paper: #ffffff;
    --gold: #f1d19d;
    --gold-soft: #f8e6c8;
    --maroon: #7a1420;
    --ink: #3a3a3a;
    --ink-soft: #555555;
  }
  * { box-sizing: border-box; margin: 0; padding: 0; }
  html, body {
    width: 1200px; height: 417px; overflow: hidden;
    background: var(--backdrop);
    font-family: "Tinos", "Times New Roman", serif;
  }
  .canvas { position: relative; width: 1200px; height: 417px; }

  .card {
    position: absolute; top: 60px; width: 516px; height: 296px;
    display: flex; box-shadow: 0 3px 8px rgba(0,0,0,.25);
  }
  .card--front { left: 54px; }
  .card--back { left: 629px; }

  .card__brand-panel {
    width: 286px; height: 100%; background: var(--navy);
    display: flex; align-items: center; justify-content: center;
    border-right: 8px solid var(--navy);
    box-shadow: inset -3px 0 0 var(--gold);
  }
  .brand-name {
    color: var(--gold);
    font-size: 24px; font-weight: 400; letter-spacing: 1px;
    text-transform: uppercase; white-space: nowrap;
  }

  .card__info-panel {
    position: relative; flex: 1; height: 100%; background: var(--paper);
    border-left: 2px solid var(--navy);
    overflow: hidden;
  }
  .ornament {
    position: absolute; left: 14px; right: 14px; height: 44px;
    background: linear-gradient(90deg, var(--gold-soft) 0%, var(--gold) 50%, var(--gold-soft) 100%);
    border-radius: 22px;
  }
  .ornament--top { top: 8px; }
  .ornament--bottom { bottom: 8px; }

  .contact { position: absolute; left: 48px; top: 63px; color: var(--ink); }
  .contact__name {
    color: var(--maroon); font-weight: 700; font-size: 17px; letter-spacing: .3px;
  }
  .contact__title { font-size: 13px; color: var(--ink-soft); margin-top: 1px; }
  .contact__address { font-size: 13px; line-height: 16px; margin-top: 16px; }
  .contact__list { list-style: none; margin-top: 8px; font-size: 13px; }
  .contact__list li { display: flex; align-items: center; height: 20px; }
  .contact__list svg { width: 10px; height: 10px; margin-right: 7px; fill: var(--maroon); flex: none; }

  .web-only {
    position: absolute; top: 144px; left: 0; right: 0; text-align: center;
    font-size: 12.5px; letter-spacing: 2.4px; color: var(--ink);
  }
</style>
</head>
<body>
<main class="canvas">

  <section class="card card--front">
    <div class="card__brand-panel">
      <span class="brand-name">Marlow &amp; Quince</span>
    </div>
    <div class="card__info-panel">
      <div class="ornament ornament--top" role="img" aria-label="Gold floral flourish ornament"></div>
      <div class="contact">
        <p class="contact__name">YOUR NAME</p>
        <p class="contact__title">Title</p>
        <p class="contact__address">00, Complex name<br>City, State 000 000</p>
        <ul class="contact__list">
          <li><svg viewBox="0 0 10 10"><circle cx="5" cy="5" r="5"/><path d="M3 2.5h1.3l.5 1.4-.8.6a4 4 0 0 0 1.5 1.5l.6-.8 1.4.5V7a.6.6 0 0 1-.7.5A5 5 0 0 1 2.5 3.2.6.6 0 0 1 3 2.5z" fill="#fff"/></svg>+2347015550142</li>
          <li><svg viewBox="0 0 10 10"><rect x="2.5" y="0" width="5" height="10" rx="1"/><rect x="3.3" y="1.2" width="3.4" height="6" fill="#fff"/><circle cx="5" cy="8.6" r=".6" fill="#fff"/></svg>+2347015550142</li>
          <li><svg viewBox="0 0 10 10"><rect x="0" y="2" width="10" height="6.5" rx=".6"/><path d="M.5 2.6 5 5.8l4.5-3.2" stroke="#fff" stroke-width=".8" fill="none"/></svg>hello@marlowquince.com</li>
          <li><svg viewBox="0 0 10 10"><circle cx="5" cy="5" r="5"/><path d="M0 5h10M5 0c-2.5 2.8-2.5 7.2 0 10M5 0c2.5 2.8 2.5 7.2 0 10" stroke="#fff" stroke-width=".7" fill="none"/></svg>www.marlowquince.com</li>
        </ul>
      </div>
      <div class="ornament ornament--bottom" role="img" aria-label="Gold floral flourish ornament"></div>
    </div>
  </section>

  <section class="card card--back">
    <div class="card__brand-panel">
      <span class="brand-name">Marlow &amp; Quince</span>
    </div>
    <div class="card__info-panel">
      <div class="ornament ornament--top" role="img" aria-label="Gold floral flourish ornament"></div>
      <p class="web-only">www.marlowquince.com</p>
      <div class="ornament ornament--bottom" role="img" aria-label="Gold floral flourish ornament"></div>
    </div>
  </section>

</main>
</body>
</html>
```